WOW me! Employment Ad needed!

We are seeking a custom, elegant, modern and attractive ad for new employees. I have attached our logo and content of the ad.

Target Market(s)

Insurance adjusters

Industry/Entity Type

Insurance

Colors

Designer to choose colors to be used in the design.

```html
<!DOCTYPE html>
<html lang="en">
<head>
<meta charset="utf-8">
<title>Harbor Crest – Independent Adjusters Wanted</title>
<link rel="stylesheet" href="https://fonts.googleapis.com/css2?family=Roboto+Condensed:wght@400;700&family=Roboto:wght@400;700&display=swap">
<style>
  :root{
    --navy-deep:#0f2447;
    --navy:#163766;
    --blue-sky:#3f6fae;
    --haze:#c9d6e8;
    --orange:#f47a20;
    --orange-light:#ff9a4a;
    --white:#ffffff;
    --ink:#1a1a1a;
    --logo-navy:#1b3a78;
  }
  *{margin:0;padding:0;box-sizing:border-box}
  html,body{width:727px;height:1200px;overflow:hidden;background:#e8eef7}
  .ad{
    position:relative;width:727px;height:1200px;overflow:hidden;
    background:linear-gradient(180deg,#1d4780 0%,var(--navy) 35%,var(--navy-deep) 70%,var(--navy-deep) 100%);
    font-family:"Roboto",Arial,sans-serif;color:var(--white);
  }
  .hero-photo{
    position:absolute;top:0;right:0;width:400px;height:620px;
    background:
      radial-gradient(circle at 55% 12%,rgba(255,190,120,.75) 0,rgba(255,190,120,0) 22%),
      linear-gradient(200deg,#e9eef6 0%,var(--haze) 30%,#7f9cc4 55%,rgba(22,55,102,0) 90%);
    -webkit-mask-image:linear-gradient(90deg,transparent 0,#000 35%);
            mask-image:linear-gradient(90deg,transparent 0,#000 35%);
  }
  .headline{
    position:absolute;left:75px;top:62px;
    font-family:"Roboto Condensed",Arial,sans-serif;font-weight:400;
    font-size:43px;line-height:54px;text-transform:uppercase;letter-spacing:-.3px;
  }
  .headline .accent{color:var(--orange)}
  .headline-rule{position:absolute;left:75px;top:356px;width:153px;height:4px;background:var(--orange)}
  .intro{
    position:absolute;left:75px;top:396px;width:290px;
    font-size:11px;line-height:14.5px;text-align:justify;
  }
  .intro p{margin-bottom:13px}
  .perks{
    position:absolute;left:75px;top:766px;width:290px;height:86px;
    border:1px solid rgba(255,255,255,.75);border-radius:6px;
    display:flex;gap:8px;padding:12px 12px 0 14px;font-size:11px;line-height:13.5px;list-style:none;
  }
  .perks li,.requirements li{position:relative;padding-left:15px}
  .perks li{flex:1}
  .tick{position:absolute;left:0;top:2px;width:9px;height:9px}
  .apply{
    position:absolute;left:35px;top:896px;width:390px;height:135px;
    background:linear-gradient(180deg,var(--orange-light),var(--orange));
    border-top-left-radius:30px;padding:24px 0 0 34px;
    font-family:"Roboto Condensed",Arial,sans-serif;color:var(--navy-deep);
    font-size:16.5px;line-height:21px;text-transform:uppercase;
  }
  .apply .email{display:block;margin-top:4px;text-transform:none;font-weight:700;font-size:19px}
  .requirements-panel{
    position:absolute;left:412px;top:518px;width:282px;height:513px;
    background:linear-gradient(180deg,var(--orange-light) 0,var(--orange) 30%,var(--orange) 100%);
    border-radius:30px 30px 0 0;padding:30px 24px 0 30px;color:var(--navy-deep);
  }
  .requirements-panel h2{
    font-family:"Roboto Condensed",Arial,sans-serif;font-weight:400;font-size:21px;
    text-transform:uppercase;margin-bottom:18px;
  }
  .requirements{list-style:none;font-size:11px;line-height:13.5px}
  .requirements li{margin-bottom:9px}
  .footer{
    position:absolute;left:0;bottom:0;width:727px;height:169px;background:var(--white);
  }
  .brand{position:absolute;left:65px;top:30px;color:var(--logo-navy)}
  .brand-name{
    font-family:"Roboto Condensed",Arial,sans-serif;font-weight:700;font-size:70px;line-height:66px;
    letter-spacing:1px;
  }
  .brand-tagline{font-size:11px;color:var(--orange);margin-top:2px;letter-spacing:.2px}
  .contact{
    position:absolute;left:384px;top:52px;color:var(--ink);
    font-weight:700;font-size:17px;line-height:32px;letter-spacing:3px;
  }
</style>
</head>
<body>
<main class="ad">
  <div class="hero-photo" role="img" aria-label="Businessman in a suit holding an umbrella, seen from behind against a sunlit city skyline"></div>

  <h1 class="headline">
    Specializing in<br>
    <span class="accent">Indepent Adjusting</span><br>
    <span class="accent">Service</span> in<br>
    New York State<br>
    and Mass
  </h1>
  <div class="headline-rule"></div>

  <section class="intro">
    <p>Harbor Crest Claim Service, Inc. (CREST) is the premier independent insurance adjusting company throughout the Northeastern United States. We provide both full-service liability and property insurance claims adjusting along with catastrophe property adjustment services to insurance carriers doing business throughout the United States.</p>
    <p>CREST is a New York based corporation headquartered in the Albany, New York region.</p>
    <p>We are currently seeking New York State licensed Independent Insurance Adjusters with lines of authority to be, at minimum, “Fire”, however, “General” is preferred.</p>
    <p>1099 Adjusters are non-employee contractors that will investigate and evaluate property claims for clients pursuant to CREST standards. This position will provide timely, accurate, fair, and professional service to all clients and insured parties while maintaining carrier specific service level agreement standards.</p>
  </section>

  <ul class="perks">
    <li><svg class="tick" viewBox="0 0 10 10"><circle cx="5" cy="5" r="4.3" fill="none" stroke="#f47a20" stroke-width="1.2"/><path d="M3 5.2l1.5 1.4L7.2 3.8" fill="none" stroke="#f47a20" stroke-width="1.2"/></svg>CREST offers an exceptional industry leading compensation program.</li>
    <li><svg class="tick" viewBox="0 0 10 10"><circle cx="5" cy="5" r="4.3" fill="none" stroke="#f47a20" stroke-width="1.2"/><path d="M3 5.2l1.5 1.4L7.2 3.8" fill="none" stroke="#f47a20" stroke-width="1.2"/></svg>CREST is an Equal Opportunity Employer.</li>
  </ul>

  <section class="apply">
    Send resume and copy of drivers license<br>
    and New York State IA license to:
    <span class="email">joinourteam@crestadjusters.com</span>
  </section>

  <section class="requirements-panel">
    <h2>Job Requirements:</h2>
    <ul class="requirements">
      <li><svg class="tick" viewBox="0 0 10 10"><circle cx="5" cy="5" r="4.3" fill="none" stroke="#0f2447" stroke-width="1"/><path d="M3 5.2l1.5 1.4L7.2 3.8" fill="none" stroke="#0f2447" stroke-width="1"/></svg>Experience preparing estimates with Estimax, Claimly and/or Scopewise.</li>
      <li><svg class="tick" viewBox="0 0 10 10"><circle cx="5" cy="5" r="4.3" fill="none" stroke="#0f2447" stroke-width="1"/><path d="M3 5.2l1.5 1.4L7.2 3.8" fill="none" stroke="#0f2447" stroke-width="1"/></svg>Exceptional communication and customer service skills</li>
      <li><svg class="tick" viewBox="0 0 10 10"><circle cx="5" cy="5" r="4.3" fill="none" stroke="#0f2447" stroke-width="1"/><path d="M3 5.2l1.5 1.4L7.2 3.8" fill="none" stroke="#0f2447" stroke-width="1"/></svg>High Technical aptitude</li>
      <li><svg class="tick" viewBox="0 0 10 10"><circle cx="5" cy="5" r="4.3" fill="none" stroke="#0f2447" stroke-width="1"/><path d="M3 5.2l1.5 1.4L7.2 3.8" fill="none" stroke="#0f2447" stroke-width="1"/></svg>Ability to climb ladders, get in attics/crawlspaces, get on roofs, kneel, bend, etc.</li>
      <li><svg class="tick" viewBox="0 0 10 10"><circle cx="5" cy="5" r="4.3" fill="none" stroke="#0f2447" stroke-width="1"/><path d="M3 5.2l1.5 1.4L7.2 3.8" fill="none" stroke="#0f2447" stroke-width="1"/></svg>A valid driver’s license</li>
      <li><svg class="tick" viewBox="0 0 10 10"><circle cx="5" cy="5" r="4.3" fill="none" stroke="#0f2447" stroke-width="1"/><path d="M3 5.2l1.5 1.4L7.2 3.8" fill="none" stroke="#0f2447" stroke-width="1"/></svg>Have a valid New York State IA License</li>
      <li><svg class="tick" viewBox="0 0 10 10"><circle cx="5" cy="5" r="4.3" fill="none" stroke="#0f2447" stroke-width="1"/><path d="M3 5.2l1.5 1.4L7.2 3.8" fill="none" stroke="#0f2447" stroke-width="1"/></svg>Strong investigative, analytical, and problem solving skills Capability to plan, organize and manage time</li>
      <li><svg class="tick" viewBox="0 0 10 10"><circle cx="5" cy="5" r="4.3" fill="none" stroke="#0f2447" stroke-width="1"/><path d="M3 5.2l1.5 1.4L7.2 3.8" fill="none" stroke="#0f2447" stroke-width="1"/></svg>Knowledge of insurance policies, theories and practices</li>
      <li><svg class="tick" viewBox="0 0 10 10"><circle cx="5" cy="5" r="4.3" fill="none" stroke="#0f2447" stroke-width="1"/><path d="M3 5.2l1.5 1.4L7.2 3.8" fill="none" stroke="#0f2447" stroke-width="1"/></svg>Candidate must have at least one current active estimating system registered and have the ability to send electronic reports through the Internet.</li>
      <li><svg class="tick" viewBox="0 0 10 10"><circle cx="5" cy="5" r="4.3" fill="none" stroke="#0f2447" stroke-width="1"/><path d="M3 5.2l1.5 1.4L7.2 3.8" fill="none" stroke="#0f2447" stroke-width="1"/></svg>Candidate must pass background check</li>
    </ul>
  </section>

  <footer class="footer">
    <div class="brand">
      <div class="brand-name">CREST</div>
      <div class="brand-tagline">HARBOR CREST CLAIMS UNLIMITED SERVICES</div>
    </div>
    <div class="contact">
      1-800-555-0142<br>
      www.CRESTAdjusters.com
    </div>
  </footer>
</main>
</body>
</html>
```